NCCS Brochure Design

Northfield Council of Clinical Standards (NCCS) needs a whole new brochure. I've upload EPS logos and past brochures. Our tagline is to "modernize healthcare" and we think our brochure should reflect that, so that's the purpose of this project.

NCCS is a proven leader in healthcare education, training and
consulting services for health professionals. We’ve earned a reputation for excellence in healthcare quality improvement and management.

NCCS works to improve healthcare quality by educating healthcare professionals about healthcare best practices. We focus on instructing our clients on how to plan for, measure, and improve healthcare quality in all facilities and facets such as:

Patient Safety
Infection Control
Performance Improvement
Risk Management
Compliance and Accreditation
Health and Hospital Administration
Health Insurance
Healthcare Financial Management
Facility Management and Safety

DESIGN SUGGESTIONS:

Brochure Size: 8.5 X 11 full size brochure or 8.5 X 11 trifold brochure

Number of Pages: 2 to 3

Colors: Feel free to use a wide array of colors but try to stay away from colors that are too loud, ex: Pink, Purple, Neon Green.

Themes: Professional, Educational

Designs:

Pelvor by Tobin Haskell

Lumora Leaflet by Derek Molloy

Gears of assembly by Vostrelle

Figura de Mr KB by qzpt

http://www.plimvaro.com/post/28461937520/10-creative-brochure-designs

Don't limit yourself to these examples. However, these are examples we liked

Reason: We would like to see more designs

We want more full page designs than tri-fold 

We are considering both tri-fold and full-page but would like to see more full page designs 

Reason: Our lead designer making the decisions on this project has been fired. I apologize for the inconvenience. We want extend the project one last time

Target Market(s)

Students, Doctors, and Educational Professionals

Industry/Entity Type

Healthcare

Font styles to use
Serif
Sans Serif
Decorative
Script

Requirements
Should not have
• Pink, Purple, Neon Green colors

```html
<!DOCTYPE html>
<html lang="en">
<head>
<meta charset="utf-8">
<title>NCCS Brochure</title>
<link href="https://fonts.googleapis.com/css2?family=Antonio:wght@100;300&family=Jura:wght@500;700&family=Exo+2:wght@400;500&display=swap" rel="stylesheet">
<style>
:root{
  --canvas:#eeeeee;
  --ink-dark:#2f3233;
  --band:#3b3d3e;
  --band-edge:#5a5d5e;
  --panel-mid:#b5b7b7;
  --panel-light:#d9dbdb;
  --photo-cool:#8fa3a6;
  --photo-deep:#3a4244;
  --text-light:#f2f4f4;
  --text-body:#2c2e2f;
}
*{box-sizing:border-box;margin:0;padding:0}
html,body{width:1200px;height:1000px;overflow:hidden;background:var(--canvas)}
body{position:relative;font-family:"Exo 2",sans-serif;color:var(--text-body)}
.spread{position:absolute;left:28px;top:176px;width:840px;height:648px;display:flex;box-shadow:0 2px 10px rgba(0,0,0,.15)}
.panel{position:relative;width:280px;height:648px;overflow:hidden}
.heading{font-family:"Jura",sans-serif;font-weight:700;letter-spacing:3px;text-transform:uppercase}

/* panel 1 */
.panel-intro{background:var(--panel-light)}
.intro-photo{position:absolute;inset:0;background:linear-gradient(100deg,#e7ebeb 0%,#c6d0d1 30%,var(--photo-cool) 55%,#4d5759 75%,#dfe3e3 100%)}
.intro-band{position:absolute;left:0;top:36px;width:250px;height:112px;background:var(--band);clip-path:polygon(0 0,100% 0,86% 100%,0 100%);padding:14px 70px 0 14px;color:var(--text-light);font-size:8.6px;line-height:1.35}
.intro-mark{position:absolute;left:196px;top:62px;display:flex;align-items:center;gap:4px;color:var(--text-light);font-family:"Jura",sans-serif;font-weight:700;font-size:11px}
.intro-mark i{width:12px;height:12px;border-radius:50%;background:var(--text-light);display:block}
.statement{position:absolute;left:12px;width:162px}
.statement h2{font-size:24px;line-height:28px;color:var(--ink-dark);font-weight:500;letter-spacing:3px;margin-bottom:2px}
.statement p{font-size:8.4px;line-height:1.3;color:var(--text-body)}
.vision{top:296px}
.mission{top:468px}

/* panel 2 */
.panel-courses{background:linear-gradient(180deg,var(--panel-mid) 0%,#c9cbcb 45%,#a4a6a6 100%)}
.tab{position:absolute;left:0;top:16px;width:280px;height:44px;background:var(--band);clip-path:polygon(0 0,94% 0,100% 100%,0 100%);color:var(--text-light);font-size:20px;padding:9px 0 0 12px}
.tab-fold{position:absolute;right:0;top:16px;width:20px;height:44px;background:var(--band-edge);clip-path:polygon(0 0,100% 20%,100% 100%,30% 100%)}
.course-list{position:absolute;left:12px;top:72px;list-style:none;font-size:8.6px;line-height:1.45;color:var(--text-body)}
.web-box{position:absolute;left:10px;top:278px;width:258px;height:54px;border:3px solid #5d6060;border-radius:12px;padding:5px 10px;white-space:nowrap;overflow:hidden}
.web-box small{display:block;font-size:8px;font-weight:500;color:var(--text-body)}
.web-box span{display:block;font-family:"Jura",sans-serif;font-size:16px;line-height:26px;color:#5a5d5e;letter-spacing:.5px}
.pointer{position:absolute;left:236px;top:310px}
.team{position:absolute;left:12px;top:356px;width:140px}
.team h2,.about h2{font-size:22px;line-height:26px;color:var(--ink-dark);font-weight:500;letter-spacing:3px}
.team p,.about p{font-size:8.4px;line-height:1.3}
.team ul{list-style:none;font-size:8.4px;line-height:1.3;margin:8px 0 0 10px}
.team-photo{position:absolute;left:152px;top:356px;width:122px;height:192px;background:linear-gradient(160deg,#f4f6f6 0%,#b9c6c8 40%,#6f9a9c 70%,#e3e6e6 100%);border:3px solid #f2f2f2;clip-path:polygon(0 8%,8% 0,100% 0,100% 100%,14% 100%,0 88%)}
.about{position:absolute;left:12px;top:558px;width:255px}

/* panel 3 */
.panel-schedule{background:linear-gradient(170deg,#6e7778 0%,#525b5c 35%,var(--photo-deep) 70%,#5e6768 100%)}
.schedule-photo{position:absolute;inset:0;background:linear-gradient(90deg,rgba(255,255,255,.05) 0 40%,rgba(0,0,0,.18) 60%,rgba(255,255,255,.08) 100%)}
.schedule-band{position:absolute;left:0;top:22px;width:280px;height:50px;background:var(--band);color:var(--panel-light);font-size:21px;padding:11px 0 0 14px}
.schedule{position:absolute;left:12px;top:192px;list-style:none;color:var(--text-light);font-size:8.4px;line-height:1.3}
.schedule li{margin-bottom:11px}

/* cover */
.cover{position:absolute;left:892px;top:176px;width:280px;height:648px;overflow:hidden;background:linear-gradient(180deg,#5b6364 0%,#7c8586 35%,#4a5253 70%,#6a7273 100%);box-shadow:0 2px 10px rgba(0,0,0,.15)}
.cover-inner{position:absolute;left:0;top:648px;width:648px;height:280px;transform-origin:0 0;transform:rotate(-90deg);padding:16px 22px}
.title{position:absolute;left:30px;top:14px;width:420px;font-family:"Antonio",sans-serif;font-weight:100;color:var(--text-light);font-size:48px;line-height:1;letter-spacing:11px}
.title span{display:block;border-bottom:1px solid rgba(255,255,255,.75);padding:3px 0}
.title span:first-child{border-top:1px solid rgba(255,255,255,.75)}
.cover-sub{position:absolute;left:30px;top:244px;font-family:"Antonio",sans-serif;font-weight:300;font-size:10px;letter-spacing:3px;color:var(--text-light)}
.cover-mark{position:absolute;left:486px;top:176px;display:flex;align-items:center;gap:6px;font-family:"Jura",sans-serif;font-weight:700;font-size:20px;color:var(--text-light)}
.cover-mark i{width:16px;height:16px;border-radius:50%;background:var(--text-light);display:block}
.cover-url{position:absolute;left:470px;top:232px;font-size:12px;color:var(--text-light);letter-spacing:.5px}
</style>
</head>
<body>
<main class="spread">
  <section class="panel panel-intro">
    <div class="intro-photo" role="img" aria-label="Photo of a nurse in motion carrying a folder down a hospital corridor"></div>
    <div class="intro-band">NCCS is a proven leader in healthcare education, training and consulting services for health professionals. We've earned a reputation for excellence in healthcare quality improvement and management.</div>
    <div class="intro-mark"><i></i>NCCS</div>
    <div class="statement vision">
      <h2 class="heading">Vision</h2>
      <p>Here at the Northfield Council of Clinical Standards, we believe that the highest quality in healthcare comes from the highest quality people. We envision a care environment that is focused on quality, enabled by healthcare professionals who have been well trained to improve healthcare outcomes, and who are as passionate as we are about improving the delivery of healthcare and the performance of organizations.</p>
    </div>
    <div class="statement mission">
      <h2 class="heading">Mission</h2>
      <p>Our mission is to enhance quality in healthcare by transforming the professionals who work in healthcare. We aim to give you the tools and knowledge that you need to impact healthcare delivery and outcomes and to be an advocate for quality and patient safety.</p>
    </div>
  </section>

  <section class="panel panel-courses">
    <h2 class="tab heading">Course Offerings</h2>
    <div class="tab-fold"></div>
    <ul class="course-list">
      <li>Certificate of Healthcare Quality (CHQ)</li>
      <li>Certified Professional in Infection Control (CPIC)</li>
      <li>Certified in Health Performance Improvement (CHPI)</li>
      <li>Certified in Healthcare Risk Management (CHRM)</li>
      <li>Certified Hospital Surveyor (CHS)</li>
      <li>Certified Professional in Health and Hospital Administration (CPHHA)</li>
      <li>Certified Patient Safety Officer (CPSO)</li>
      <li>Certified in Healthcare Financial Management (CHFM)</li>
      <li>Certified in Healthcare Insurance Administration (CHIA)</li>
      <li>Certified Facility Safety Officer (CFSO)</li>
      <li>Certified in Human Resources Management (CHRM)</li>
      <li>Certified Medication Safety Officer (CMSO)</li>
      <li>Fellowship Preparation Course (FNCCS)</li>
    </ul>
    <div class="web-box">
      <small>For detailed Courses program Please visit our website</small>
      <span>www.nccs-standards.org</span>
    </div>
    <svg class="pointer" width="30" height="34" viewBox="0 0 30 34" aria-hidden="true">
      <path d="M4 2 L4 26 L10 20 L15 31 L19 29 L14 18 L23 18 Z" fill="#ffffff" stroke="#2f3233" stroke-width="2" stroke-linejoin="round"/>
    </svg>
    <div class="team">
      <h2 class="heading">Our Team</h2>
      <p>Our outstanding Advisory Board guides NCCS's strategic direction and ensures that we maintain our laser-like focus on excellence in healthcare quality. This team includes:</p>
      <ul>
        <li>Dr. PH Wendell Crane</li>
        <li>Owen Dalby, JD</li>
        <li>Professor Samir Haddou, Ph.d</li>
        <li>Professor Glenn Marsh, Ph.d</li>
        <li>Professor Ray Colter, Ph.d</li>
        <li>Professor Evan Pritch, Ph.d</li>
      </ul>
    </div>
    <div class="team-photo" role="img" aria-label="Photo of three cheering healthcare professionals in scrubs and white coats"></div>
    <div class="about">
      <h2 class="heading">About Us</h2>
      <p>Here at the Northfield Council of Clinical Standards, we believe that the highest quality in healthcare comes from the highest quality people, trained to improve healthcare outcomes and as passionate as we are about its delivery.</p>
    </div>
  </section>

  <section class="panel panel-schedule">
    <div class="schedule-photo" role="img" aria-label="Blurred photo of a hospital corridor with motion streaks"></div>
    <h2 class="schedule-band heading">Course Schedule</h2>
    <ul class="schedule">
      <li>Certified Professional in Infection Control (CPIC)<br>January 12-16, 2014 &nbsp;| 8:00 AM – 4:00 PM<br>June 21-26, 2014</li>
      <li>Certified Hospital Surveyor (CHS)<br>February 15-19, 2014 &nbsp;| 8:00 AM – 4:00 PM<br>February 22-27, 2014</li>
      <li>Certified in Healthcare Performance Improvement (CHPI)<br>March 16-20, 2014 &nbsp;| 8:00 AM – 4:00 PM<br>March 22-27, 2014</li>
      <li>Certified Health and Hospital Administrator (CPHHA)<br>April 20-24, 2014 &nbsp;| 8:00 AM – 4:00 PM<br>April 26-30, 2014</li>
      <li>Certified Healthcare Quality (CHQ)<br>May 18-22, 2014 &nbsp;| 8:00 AM – 4:00 PM<br>May 24-28, 2014</li>
      <li>Fellow of the Northfield Council of Clinical Standards (FNCCS)<br>September 14-18, 2014 | 8:00 AM – 4:00 PM<br>September 20-25, 2014</li>
      <li>Certified Healthcare Risk Manager (CHRM)<br>October 19-23, 2014 &nbsp;| 8:00 AM – 4:00 PM<br>October 25-30, 2014</li>
    </ul>
  </section>
</main>

<section class="cover" role="img" aria-label="Cover background photo of a blurred hospital corridor">
  <div class="cover-inner">
    <h1 class="title"><span>NORTHFIELD</span><span>COUNCIL OF</span><span>CLINICAL</span><span>STANDARDS</span></h1>
    <p class="cover-sub">HEALTHCARE PROFESSIONALS</p>
    <div class="cover-mark"><i></i>NCCS</div>
    <p class="cover-url">www.nccs-standards.org</p>
  </div>
</section>
</body>
</html>
```